Holiday Club Flyer for 2026

Hi Ferncraft. We need a new flyer making for our holiday club for this year. You have made the last few which have always been good. This year the theme is space so please could you change the design to a space theme. The dates of the Holiday club are 28th, 29th and 30th October. It is the same venue, same timings and same activities that happen, we need the dates updating and the them of the flyer changing to space. I have attached last years flyer for you as a reminder.

```html
<!DOCTYPE html>
<html lang="en">
<head>
<meta charset="utf-8">
<title>Holiday Club – Space Adventure Flyer</title>
<link href="https://fonts.googleapis.com/css2?family=Rajdhani:wght@600;700&family=Roboto:wght@400;500;700&family=Exo+2:wght@800;900&display=swap" rel="stylesheet">
<style>
  :root{
    --page:#ffffff;
    --space-deep:#05070f;
    --space-mid:#0d1630;
    --space-glow:#16264d;
    --teal:#1aa3a8;
    --teal-light:#3fc6c9;
    --white:#ffffff;
    --panel:#050812;
    --panel-line:#c9ced8;
    --green:#2fae3a;
    --green-badge:#5bcb2c;
    --mars:#c9382a;
    --jupiter:#d9733a;
    --sun:#f6b81c;
    --saturn:#f0b73a;
    --ufo:#34b58c;
    --rocket:#e6e8ec;
    --moon-light:#b7b9bd;
    --moon-dark:#4b4d52;
    --earth:#1f4fb0;
    --suit:#dfe3ea;
    --star:#f7c948;
  }
  *{margin:0;padding:0;box-sizing:border-box}
  html,body{width:1200px;height:773px;overflow:hidden;background:var(--page)}
  body{position:relative;font-family:'Roboto',sans-serif;color:var(--white)}

  .flyer{position:absolute;overflow:hidden;
    background:radial-gradient(ellipse at 60% 35%,var(--space-glow) 0%,var(--space-mid) 40%,var(--space-deep) 100%)}
  .flyer--info{left:20px;top:21px;width:567px;height:733px}
  .flyer--cover{left:613px;top:19px;width:566px;height:733px}

  .abs{position:absolute}
  .planet{position:absolute;border-radius:50%}
  .layer-top{z-index:3}

  /* brand */
  .brand{left:60px;top:44px;display:flex;align-items:center;gap:10px}
  .brand__dot{width:44px;height:44px;border-radius:50%;background:var(--green);flex:none}
  .brand__name{font-family:'Rajdhani',sans-serif;font-weight:700;font-size:21px;line-height:1.05;color:var(--white)}
  .badge-free{left:258px;top:40px;width:42px;height:42px;border-radius:50%;background:var(--green-badge);
    display:flex;align-items:center;justify-content:center;font-family:'Rajdhani',sans-serif;font-weight:700;font-size:14px;color:var(--white);transform:rotate(15deg)}

  .headline-kicker{left:43px;top:118px;font-family:'Exo 2',sans-serif;font-weight:800;font-size:31px;letter-spacing:.5px}
  .headline-main{left:46px;top:163px;font-family:'Exo 2',sans-serif;font-weight:900;font-size:47px;color:var(--teal);
    text-shadow:2px 3px 0 #8e97a6;letter-spacing:.5px;white-space:nowrap}

  .card{position:absolute;background:var(--panel);border:1.5px solid var(--panel-line);border-radius:10px}
  .card__title{position:absolute;display:flex;align-items:center;gap:8px;font-family:'Rajdhani',sans-serif;font-weight:700;font-size:25px;color:var(--teal-light);letter-spacing:.5px}
  .card__title svg{flex:none}
  .card--time{left:31px;top:239px;width:261px;height:111px}
  .card--dates{left:305px;top:239px;width:235px;height:111px}
  .card--register{left:31px;top:363px;width:261px;height:83px}
  .card--location{left:305px;top:364px;width:239px;height:83px}

  .time-row{position:absolute;font-size:11px;font-weight:500;text-transform:uppercase}
  .time-value{position:absolute;font-size:14px;font-weight:500}

  .date-chip{position:absolute;top:50px;width:58px;height:50px;border:1px solid var(--panel-line);border-radius:5px;text-align:center}
  .date-chip__day{font-family:'Exo 2',sans-serif;font-weight:800;font-size:22px;line-height:1;margin-top:6px;color:#e8ebf0}
  .date-chip__day small{font-size:12px}
  .date-chip__month{font-family:'Rajdhani',sans-serif;font-weight:700;font-size:9px;letter-spacing:.5px;margin-top:3px;color:#e8ebf0}

  .card-text{position:absolute;font-size:11.5px;line-height:1.35;letter-spacing:.3px}

  .find-title{left:33px;top:479px;font-family:'Rajdhani',sans-serif;font-weight:700;font-size:24px;color:var(--teal-light)}
  .find-address{left:31px;top:512px;font-size:11.5px;line-height:20.5px;letter-spacing:.4px;text-transform:uppercase}
  .find-email{left:31px;top:575px;display:flex;align-items:center;gap:10px;font-family:'Rajdhani',sans-serif;font-weight:600;font-size:11.5px;color:var(--teal-light)}

  .features{left:324px;top:478px;list-style:none}
  .features li{display:flex;align-items:center;gap:10px;height:26px;font-size:13.5px;letter-spacing:.6px}

  .moonscape{left:0;top:596px;width:567px;height:137px;background:linear-gradient(180deg,#8d9096 0%,#5c5f65 55%,#2f3136 100%)}
  .rover{left:120px;top:604px;width:290px;height:129px;border-radius:8px 8px 0 0;background:linear-gradient(180deg,#c9ccd2,#6f6a5c)}
  .age-badge{left:412px;top:584px;width:110px;height:110px;border-radius:50%;
    background:radial-gradient(circle at 40% 40%,#2f64c8,var(--earth) 60%,#0b1c4a);
    display:flex;align-items:center;justify-content:center;text-align:center;
    font-family:'Rajdhani',sans-serif;font-weight:700;font-size:16px;line-height:1.3}

  /* cover */
  .cover-title{left:0;width:566px;text-align:center;font-family:'Exo 2',sans-serif;font-weight:900;white-space:nowrap}
  .cover-title--space{top:155px;font-size:92px;letter-spacing:8px;
    background:linear-gradient(180deg,#ffffff 0%,#c7c7cc 45%,#8d8b92 100%);-webkit-background-clip:text;background-clip:text;color:transparent;
    filter:drop-shadow(3px 3px 0 #3a3a40)}
  .cover-title--adventures{top:268px;font-size:56px;letter-spacing:9px;color:var(--teal);padding-left:10px}
  .cover-moon{left:-40px;top:598px;width:646px;height:420px;border-radius:50%;
    background:radial-gradient(ellipse at 50% 20%,var(--moon-light),var(--moon-dark) 75%)}
  .cover-crew{left:92px;top:362px;width:352px;height:340px;border-radius:40% 40% 12px 12px;
    background:linear-gradient(180deg,var(--suit),#9aa3b3)}
  .cover-rocket{left:456px;top:346px;width:104px;height:278px;border-radius:50% 50% 30% 30%;
    background:linear-gradient(180deg,var(--rocket) 0%,#d6423a 70%,#f39a2a 100%)}
  .cover-ufo{left:27px;top:355px;width:62px;height:26px;border-radius:50%;background:var(--ufo)}
  .cover-saturn{left:418px;top:88px;width:100px;height:40px;border-radius:50%;background:var(--saturn);transform:rotate(-20deg)}
</style>
</head>
<body>

<section class="flyer flyer--info">
  <div class="abs brand">
    <span class="brand__dot"></span>
    <span class="brand__name">Northgate<br>holiday club</span>
  </div>
  <div class="abs badge-free">FREE!</div>
  <div class="planet" style="left:474px;top:71px;width:60px;height:60px;background:var(--jupiter)" role="img" aria-label="Illustrated banded planet"></div>

  <h2 class="abs headline-kicker">JOIN US FOR A</h2>
  <h1 class="abs headline-main">SPACE ADVENTURE!</h1>

  <div class="card card--time">
    <div class="card__title" style="left:16px;top:12px">
      <svg width="30" height="30" viewBox="0 0 30 30"><circle cx="15" cy="15" r="13" fill="#14306b" stroke="#e23b3b" stroke-width="3"/><path d="M15 7v8l5 3" stroke="#fff" stroke-width="2" fill="none" stroke-linecap="round"/></svg>
      TIME
    </div>
    <span class="time-row" style="left:18px;top:52px">Drop off from</span>
    <span class="time-value" style="left:181px;top:48px">8.45 AM</span>
    <span class="time-row" style="left:16px;top:78px">Collect your children</span>
    <span class="time-value" style="left:181px;top:74px">12.30 PM</span>
  </div>

  <div class="card card--dates">
    <div class="card__title" style="left:16px;top:12px">
      <svg width="26" height="24" viewBox="0 0 26 24"><rect x="1" y="3" width="24" height="20" rx="2" fill="#fff"/><rect x="1" y="3" width="24" height="6" fill="#e23b3b"/><g fill="#1c3f8c"><rect x="4" y="11" width="4" height="3"/><rect x="11" y="11" width="4" height="3"/><rect x="18" y="11" width="4" height="3"/><rect x="4" y="16" width="4" height="3"/><rect x="11" y="16" width="4" height="3"/><rect x="18" y="16" width="4" height="3"/></g></svg>
      &nbsp;DATES
    </div>
    <div class="date-chip" style="left:20px"><div class="date-chip__day">28<small>TH</small></div><div class="date-chip__month">OCTOBER</div></div>
    <div class="date-chip" style="left:92px"><div class="date-chip__day">29<small>TH</small></div><div class="date-chip__month">OCTOBER</div></div>
    <div class="date-chip" style="left:164px"><div class="date-chip__day">30<small>TH</small></div><div class="date-chip__month">OCTOBER</div></div>
  </div>

  <div class="card card--register">
    <div class="card__title" style="left:18px;top:12px">
      <svg width="28" height="28" viewBox="0 0 28 28"><path d="M25 3c-7 0-12 4-15 10l5 5c6-3 10-8 10-15z" fill="#e6e8ec"/><circle cx="18" cy="10" r="3" fill="#2d7be0"/><path d="M10 13l-6 1 3 3zM15 18l-1 6-3-3z" fill="#e23b3b"/><path d="M8 20l-4 4 1-5z" fill="#f39a2a"/></svg>
      REGISTER AT
    </div>
    <span class="card-text" style="left:18px;top:54px">https://northgate.church/holiday-club</span>
  </div>

  <div class="card card--location">
    <div class="card__title" style="left:20px;top:12px">
      <svg width="22" height="28" viewBox="0 0 22 28"><path d="M11 1C5.5 1 1.5 5 1.5 10.5 1.5 17 11 26 11 26s9.5-9 9.5-15.5C20.5 5 16.5 1 11 1z" fill="#e8452f"/><circle cx="11" cy="10.5" r="4" fill="#fff"/></svg>
      LOCATION
    </div>
    <span class="card-text" style="left:18px;top:48px">NORTHGATE CHAPEL Harbour<br>Lane Road</span>
  </div>

  <div class="abs moonscape" role="img" aria-label="Photograph of the lunar surface"></div>
  <div class="abs rover" role="img" aria-label="Photograph of a lunar rover on the moon"></div>

  <h3 class="abs find-title layer-top">FIND US</h3>
  <p class="abs find-address layer-top">Northgate Chapel,<br>Harbour Lane Road,<br>Aldbury, AB1 2CD</p>
  <div class="abs find-email layer-top">
    <svg width="16" height="14" viewBox="0 0 16 14"><rect x="0" y="3" width="16" height="11" rx="1" fill="#f29a2e"/><path d="M0 4l8 5 8-5" stroke="#c96a10" fill="none"/><circle cx="8" cy="4" r="3.5" fill="#e23b3b"/></svg>
    sam@northgatechapel.org
  </div>

  <div class="planet" style="left:260px;top:478px;width:34px;height:34px;background:var(--mars)" role="img" aria-label="Illustrated red planet"></div>

  <ul class="abs features layer-top">
    <li><svg width="14" height="14" viewBox="0 0 14 14"><path d="M7 0l1.6 5.4L14 7l-5.4 1.6L7 14l-1.6-5.4L0 7l5.4-1.6z" fill="var(--star)"/></svg>Featuring games,</li>
    <li><svg width="14" height="14" viewBox="0 0 14 14"><path d="M7 0l1.6 5.4L14 7l-5.4 1.6L7 14l-1.6-5.4L0 7l5.4-1.6z" fill="var(--star)"/></svg>bible stories,</li>
    <li><svg width="14" height="14" viewBox="0 0 14 14"><path d="M7 0l1.6 5.4L14 7l-5.4 1.6L7 14l-1.6-5.4L0 7l5.4-1.6z" fill="var(--star)"/></svg>quizzes, craft &amp; more!</li>
    <li><svg width="14" height="14" viewBox="0 0 14 14"><path d="M7 0l1.6 5.4L14 7l-5.4 1.6L7 14l-1.6-5.4L0 7l5.4-1.6z" fill="var(--star)"/></svg>Picnic lunch is included</li>
  </ul>

  <div class="abs age-badge layer-top">RECEPTION<br>TO<br>YEAR 6</div>
</section>

<section class="flyer flyer--cover">
  <div class="planet" style="left:237px;top:34px;width:74px;height:74px;background:var(--sun)" role="img" aria-label="Illustrated smiling sun"></div>
  <div class="planet" style="left:45px;top:79px;width:34px;height:34px;background:var(--mars)" role="img" aria-label="Illustrated red planet"></div>
  <div class="abs cover-saturn" role="img" aria-label="Illustrated ringed planet"></div>

  <h1 class="abs cover-title cover-title--space">SPACE</h1>
  <h2 class="abs cover-title cover-title--adventures">ADVENTURES</h2>

  <div class="abs cover-ufo" role="img" aria-label="Illustrated flying saucer"></div>
  <div class="abs cover-moon" role="img" aria-label="Illustrated cratered moon surface"></div>
  <div class="abs cover-crew" role="img" aria-label="Illustration of three child astronauts standing on the moon, one holding a toy rocket"></div>
  <div class="abs cover-rocket" role="img" aria-label="Illustrated rocket launching"></div>
</section>

</body>
</html>
```